Whitcombe Business Card Design

The name of the business is Dario Whitcombe, CPA LLC
The service that we offer is Accounting, Tax & Consulting Services. I need it to have the following items:
Dario Whitcombe, Principal
Phone Number
Email Address
Physical Address

I have attached the company logo, one in black and one in white. Please provide a design in black background and the other in white background. Please include "Accounting, Tax & Consulting Services". I want the business card to be clean and very professional.

```html
<!DOCTYPE html>
<html lang="en">
<head>
<meta charset="utf-8">
<title>Dario Whitcombe, CPA LLC — Business Card</title>
<link rel="stylesheet" href="https://fonts.googleapis.com/css2?family=Montserrat:wght@400;500;600;700&display=swap">
<style>
  :root {
    --bg: #151516;
    --card: #1f2021;
    --red: #a31d22;
    --grey: #707070;
    --light-grey: #9a9a9a;
    --white: #f2f2f2;
  }
  * { margin: 0; padding: 0; box-sizing: border-box; }
  html, body { width: 1200px; height: 988px; overflow: hidden; }
  body {
    background: var(--bg);
    font-family: "Montserrat", Arial, sans-serif;
    position: relative;
  }
  .card {
    position: absolute;
    left: 220px;
    width: 760px;
    height: 434px;
    background: var(--card);
    overflow: hidden;
    box-shadow: 0 10px 30px rgba(0,0,0,.5);
  }
  .card--front { top: 42px; }
  .card--back { top: 512px; }

  /* Front */
  .brand {
    position: absolute;
    display: flex;
    align-items: center;
    gap: 14px;
  }
  .card--front .brand { left: 150px; top: 150px; }
  .brand__square {
    width: 46px; height: 46px;
    background: var(--red);
    flex: none;
  }
  .brand__name {
    color: var(--grey);
    font-weight: 600;
    font-size: 30px;
    letter-spacing: 1px;
    text-transform: uppercase;
    white-space: nowrap;
  }
  .descriptor {
    position: absolute;
    color: var(--light-grey);
    font-weight: 600;
    text-transform: uppercase;
    letter-spacing: 3px;
    white-space: nowrap;
  }
  .card--front .descriptor { left: 210px; top: 206px; font-size: 21px; }
  .services {
    position: absolute;
    left: 210px; top: 248px;
    color: var(--light-grey);
    font-weight: 700;
    font-size: 18px;
    white-space: nowrap;
  }

  /* Back */
  .holder {
    position: absolute;
    right: 40px; top: 40px;
    color: var(--red);
    font-weight: 700;
    font-size: 22px;
    text-transform: uppercase;
    letter-spacing: .5px;
    white-space: nowrap;
  }
  .card--back .brand { left: 70px; top: 150px; gap: 10px; }
  .card--back .brand__square { width: 28px; height: 28px; }
  .card--back .brand__name { font-size: 18px; }
  .card--back .descriptor { left: 108px; top: 186px; font-size: 12px; letter-spacing: 2px; }

  .address {
    position: absolute;
    right: 40px; top: 190px;
    color: var(--white);
    font-size: 17px;
    font-style: normal;
    line-height: 1.7;
    text-align: left;
    white-space: nowrap;
  }
  .contacts {
    position: absolute;
    left: 0; bottom: 40px;
    list-style: none;
  }
  .contact {
    display: flex;
    align-items: center;
    gap: 18px;
    margin-top: 10px;
    color: var(--white);
    font-size: 17px;
    white-space: nowrap;
  }
  .contact__tab {
    width: 64px; height: 34px;
    background: var(--red);
    border-radius: 0 8px 8px 0;
    display: flex;
    align-items: center;
    justify-content: flex-end;
    padding-right: 14px;
  }
  .contact__tab svg { width: 18px; height: 18px; fill: var(--white); }
</style>
</head>
<body>

<section class="card card--front" aria-label="Card front">
  <div class="brand">
    <span class="brand__square"></span>
    <span class="brand__name">Dario Whitcombe, CPA LLC</span>
  </div>
  <p class="descriptor">Certified Public Accountant</p>
  <p class="services">Accounting, Tax &amp; Consulting Services</p>
</section>

<section class="card card--back" aria-label="Card back">
  <h1 class="holder">Dario Whitcombe, Principal</h1>

  <div class="brand">
    <span class="brand__square"></span>
    <span class="brand__name">Dario Whitcombe, CPA LLC</span>
  </div>
  <p class="descriptor">Certified Public Accountant</p>

  <address class="address">4820 Linden Park Drive<br>Suite 318</address>

  <ul class="contacts">
    <li class="contact">
      <span class="contact__tab">
        <svg viewBox="0 0 24 24" aria-hidden="true"><path d="M6.6 10.8a15.1 15.1 0 0 0 6.6 6.6l2.2-2.2a1 1 0 0 1 1-.25 11.4 11.4 0 0 0 3.6.57 1 1 0 0 1 1 1V20a1 1 0 0 1-1 1A17 17 0 0 1 3 4a1 1 0 0 1 1-1h3.5a1 1 0 0 1 1 1c0 1.25.2 2.45.57 3.57a1 1 0 0 1-.25 1z"/></svg>
      </span>
      <span>555-014-2290</span>
    </li>
    <li class="contact">
      <span class="contact__tab">
        <svg viewBox="0 0 24 24" aria-hidden="true"><path d="M2 5h20v14H2zm2 2v.5l8 5 8-5V7l-8 5z"/></svg>
      </span>
      <span>info@dariowhitcombecpa.com</span>
    </li>
    <li class="contact">
      <span class="contact__tab">
        <svg viewBox="0 0 24 24" aria-hidden="true"><path d="M12 2a10 10 0 1 0 0 20 10 10 0 0 0 0-20zm6.9 6h-3a15 15 0 0 0-1.3-3.9A8 8 0 0 1 18.9 8zM12 4c.8 1.1 1.5 2.5 1.9 4h-3.8c.4-1.5 1.1-2.9 1.9-4zM4.3 14a8 8 0 0 1 0-4h3.4a16 16 0 0 0 0 4zm.8 2h3a15 15 0 0 0 1.3 3.9A8 8 0 0 1 5.1 16zm3-8h-3a8 8 0 0 1 4.3-3.9A15 15 0 0 0 8.1 8zM12 20c-.8-1.1-1.5-2.5-1.9-4h3.8c-.4 1.5-1.1 2.9-1.9 4zm2.3-6H9.7a14 14 0 0 1 0-4h4.6a14 14 0 0 1 0 4zm.3 5.9a15 15 0 0 0 1.3-3.9h3a8 8 0 0 1-4.3 3.9zm1.7-5.9a16 16 0 0 0 0-4h3.4a8 8 0 0 1 0 4z"/></svg>
      </span>
      <span>www.dariowhitcombecpa.com</span>
    </li>
  </ul>
</section>

</body>
</html>
```